Social Media App Needs PPT Template

We need a PowerPoint template for a new social media company based in the DC area called "Bold Ledger." We provide an interactive digital platform for executives to share actionable advice. We would like to see designs that use our orange logo color as an accent, but are mainly grey, white, and black. The final design should communicate clean, chic, modern, and professional.

Target Market(s)

Executives

Industry/Entity Type

Information Technology

Font styles to use
Sans Serif

Colors
f78f20
fbe7d2
ffffff
000000
e8e8e8
757575

Requirements
Must have
• My project must have title page and many options for the body of the ppt (graphs, tables, etc). It also needs to be easy to modify. I must have someone who is experienced in creating powerpoint templates.
Nice to have
• It would be nice to have a very modern and clean design that includes the logo on every page, but still leaves a lot of room for the content of the slide
Should not have
• My design project should not look to busy.

```html
<!DOCTYPE html>
<html lang="en">
<head>
<meta charset="utf-8">
<title>Bold Ledger – About Our Company</title>
<link href="https://fonts.googleapis.com/css2?family=Lato:wght@300;400;700&display=swap" rel="stylesheet">
<style>
  :root {
    --orange: #f78f20;
    --orange-deep: #e8841a;
    --orange-soft: #fbe7d2;
    --white: #ffffff;
    --black: #000000;
    --light: #e8e8e8;
    --grey: #757575;
    --backdrop: #959595;
  }
  * { margin: 0; padding: 0; box-sizing: border-box; }
  html, body {
    width: 1200px; height: 960px; overflow: hidden;
    background: var(--backdrop);
    font-family: "Lato", sans-serif;
  }
  .canvas { position: relative; width: 1200px; height: 960px; }
  .slide {
    position: absolute; left: 68px; top: 106px; width: 1062px; height: 797px;
    background: radial-gradient(ellipse at 50% 35%, var(--white) 0%, #f3f3f3 70%, #eeeeee 100%);
  }
  .shapes { position: absolute; inset: 0; }
  .slide-title {
    position: absolute; left: 100px; top: 174px;
    font-weight: 300; font-size: 41px; color: var(--white); letter-spacing: 0.3px;
  }
  .brand {
    position: absolute; left: 934px; top: 180px;
    display: flex; align-items: center; gap: 10px;
  }
  .brand-dot { width: 26px; height: 26px; border-radius: 50%; background: var(--orange); }
  .brand-name { font-weight: 700; font-size: 24px; color: var(--white); line-height: 1; }
  .col-head, .cell, .row-label { position: absolute; line-height: 1; }
  .col-head {
    top: 390px; width: 80px; margin-left: -40px; text-align: center;
    font-size: 17px; font-weight: 400; color: #8a8a8a;
  }
  .row-label { left: 223px; font-size: 20px; }
  .cell { width: 120px; margin-left: -60px; text-align: center; font-size: 32px; font-weight: 300; }
  .row-dark { color: var(--white); }
  .row-light { color: #555555; }
  .footer-text {
    position: absolute; left: 97px; top: 869px;
    font-size: 14px; font-weight: 300; color: var(--white);
  }
  .footer-text .sep { margin: 0 8px; }
</style>
</head>
<body>
<div class="canvas">
  <div class="slide"></div>

  <svg class="shapes" width="1200" height="960" viewBox="0 0 1200 960" aria-hidden="true">
    <!-- header -->
    <polygon points="892,142 1130,142 1130,152 882,152" fill="var(--orange)"/>
    <polygon points="68,156 876,156 792,240 68,240" fill="var(--orange-deep)"/>
    <polygon points="712,156 876,156 820,212 644,212" fill="var(--orange)" opacity="0.55"/>
    <polygon points="68,222 810,222 792,240 68,240" fill="var(--orange)" opacity="0.6"/>
    <polygon points="882,156 1130,156 1130,240 798,240" fill="var(--black)"/>
    <polygon points="68,244 784,244 774,254 68,254" fill="var(--black)"/>

    <!-- table -->
    <line x1="122" y1="357" x2="1088" y2="357" stroke="#8c8c8c" stroke-width="1.2"/>
    <rect x="121" y="441" width="967" height="83" fill="var(--black)"/>
    <rect x="121" y="607" width="967" height="83" fill="var(--black)"/>

    <!-- footer -->
    <polygon points="68,861 372,861 340,892 68,892" fill="var(--black)"/>
    <polygon points="376,861 1130,861 1130,892 344,892" fill="var(--orange-deep)"/>
  </svg>

  <h1 class="slide-title">About Our Company</h1>

  <div class="brand">
    <span class="brand-dot"></span>
    <span class="brand-name">Bold Ledger</span>
  </div>

  <span class="col-head" style="left:566px">A</span>
  <span class="col-head" style="left:772px">B</span>
  <span class="col-head" style="left:978px">C</span>

  <span class="row-label row-dark" style="top:472px">Type 1</span>
  <span class="cell row-dark" style="left:566px;top:463px">20</span>
  <span class="cell row-dark" style="left:772px;top:463px">30</span>
  <span class="cell row-dark" style="left:978px;top:463px">40</span>

  <span class="row-label row-light" style="top:559px">Type 2</span>
  <span class="cell row-light" style="left:566px;top:550px">50</span>
  <span class="cell row-light" style="left:772px;top:550px">60</span>
  <span class="cell row-light" style="left:978px;top:550px">70</span>

  <span class="row-label row-dark" style="top:642px">Type 3</span>
  <span class="cell row-dark" style="left:566px;top:633px">80</span>
  <span class="cell row-dark" style="left:772px;top:633px">90</span>
  <span class="cell row-dark" style="left:978px;top:633px">100</span>

  <p class="footer-text">www.boldledger.com<span class="sep">|</span>Page 7</p>
</div>
</body>
</html>
```